UL Aesthetic improvement on full website

brightneighbourhq.com
We need someone to improve the current website brightneighbourhq.com
Some designed to fail to follow isntruction and deliver. please find attached summary latest design requirement, please follow and read each of the requirements carefully and submit max two versions only. The winner would have to deliver within 5 days

Sample reference : velmorq.com/html/brightneighbour/#
(previous winner cant deliver)
*All of our wording and graphic content are updated, designer wouldn't involve in recreating any content.
Designer may use template or own material. delivery in html and implement on our WordPress server

please submit about us the project submission.
upon the winning, you have to maintain sub content / pages and submit the full site with your improved version of full websites including inner pages

Low design quality

Target Market(s)

general audience

Industry/Entity Type

social service

Number of Pages Required

5+ page

Requirements
Must have
• feeling and look similar to pobrix dot com
Nice to have
• extend the same style to other pages

```html
<!DOCTYPE html>
<html lang="en">
<head>
<meta charset="utf-8">
<title>Bright Neighbour — New way of Giving</title>
<link rel="stylesheet" href="https://fonts.googleapis.com/css2?family=Poppins:wght@400;500;600;700&display=swap">
<style>
:root{
  --pink:#f25c62;
  --pink-soft:#fbe4e5;
  --ink:#1e1f2b;
  --body:#6b6d78;
  --line:#e6e6ea;
  --lav:#f4f3fb;
  --white:#ffffff;
}
*{box-sizing:border-box;margin:0;padding:0}
html,body{width:1200px;height:4295px;overflow:hidden}
body{font-family:"Poppins",sans-serif;color:var(--body);background:var(--white);position:relative}
.abs{position:absolute}
a{color:inherit;text-decoration:none}

.hero-bg{left:0;top:0;width:1200px;height:760px;background:linear-gradient(180deg,#fff 0%,#fff 55%,var(--lav) 100%)}
.brand{display:flex;align-items:center;gap:10px;font-weight:600;color:var(--pink);font-size:15px}
.brand-dot{width:30px;height:30px;border-radius:50%;background:var(--pink)}
.nav-links{top:36px;left:385px;display:flex;gap:32px;font-size:13px;font-weight:500;color:var(--ink)}
.nav-links .active{color:var(--pink)}
.btn{background:var(--pink);color:#fff;border-radius:22px;font-weight:600;font-size:13px;display:flex;align-items:center;justify-content:center;box-shadow:0 6px 14px rgba(242,92,98,.25)}

.h1{font-size:47px;font-weight:600;color:var(--ink);line-height:54px}
.h1 .accent{color:var(--pink)}
.lead{font-size:13px;line-height:26px;color:var(--body)}

.phones{left:520px;top:113px;width:623px;height:550px;border-radius:40px;background:radial-gradient(circle at 50% 45%,#fde7e8 0%,#f3f0fa 55%,rgba(255,255,255,0) 75%)}

.eyebrow{font-size:12px;font-weight:500;color:var(--pink)}
.partners{left:148px;top:855px;width:905px;height:393px}
.cell{position:absolute;width:181px;height:98px;border:1px solid var(--line);display:flex;align-items:center;justify-content:center;text-align:center;font-weight:600;font-size:14px;color:var(--ink);padding:0 10px;line-height:18px}

.section-title{font-size:46px;font-weight:600;color:var(--ink);text-align:center;line-height:54px;left:0;width:1200px}

.why-art{left:140px;top:1450px;width:376px;height:376px;border-radius:50%;background:linear-gradient(135deg,#f2ede6 0%,#f7c36a 45%,#2c3a8f 100%)}
.feat-icon{width:90px;height:90px;border-radius:50%;background:var(--pink);display:flex;align-items:center;justify-content:center;box-shadow:0 8px 18px rgba(242,92,98,.25)}
.feat-title{font-size:18px;font-weight:600;color:var(--ink)}
.feat-text{font-size:12.5px;line-height:27px}

.card{top:1918px;width:248px;height:285px;background:#fff;box-shadow:0 4px 18px rgba(30,31,43,.08);text-align:center;padding-top:42px}
.card h3{font-size:15px;font-weight:600;color:var(--ink);margin-top:18px}
.card p{font-size:12.5px;line-height:26.5px;margin-top:8px;padding:0 12px}
.card .more{display:block;font-size:12px;font-weight:600;color:var(--pink);margin-top:12px}

.video{left:642px;top:2313px;width:473px;height:307px;border-radius:6px;background:linear-gradient(180deg,#cfd8e4 0%,#e8b9bd 60%,#d97f86 100%);box-shadow:0 6px 18px rgba(30,31,43,.12)}

.member{top:2870px;width:248px;height:367px;background:#fff;box-shadow:0 4px 18px rgba(30,31,43,.08);text-align:center}
.member .photo{width:248px;height:247px}
.member .meta{font-size:13px;line-height:26.5px;padding-top:12px}
.member .meta b{font-weight:600;color:var(--ink);display:block}
.member.featured{background:#f47c80}
.member.featured .meta,.member.featured .meta b{color:#fff}

.gift-art{left:58px;top:3317px;width:434px;height:516px;border-radius:50%;background:radial-gradient(circle at 50% 50%,#f6d5d7 0%,#fbeff0 55%,rgba(255,255,255,0) 72%)}
.gi-title{font-size:18px;font-weight:600;color:var(--ink)}
.gi-text{font-size:12.5px;line-height:27px}
.gi-text a{color:var(--pink);font-weight:600}

.footer{left:0;top:3930px;width:1200px;height:365px;background:var(--lav)}
.f-head{font-size:13px;font-weight:600;color:var(--ink)}
.f-text{font-size:11.5px;line-height:21px}
.f-links{font-size:11.5px;line-height:30px}
.social{width:26px;height:26px;border-radius:50%;border:1.5px solid var(--pink)}
.social.solid{background:var(--pink)}
.input{left:895px;top:4080px;width:245px;height:36px;border-radius:18px;background:#fff;border:1px solid var(--line);font-size:11.5px;padding:0 16px;display:flex;align-items:center;color:#9a9ba4}
</style>
</head>
<body>

<div class="abs hero-bg"></div>
<svg class="abs" style="left:0;top:690px" width="1200" height="90" viewBox="0 0 1200 90" aria-hidden="true"><path d="M0 40 C300 0 700 80 1200 30 L1200 90 L0 90Z" fill="#fff"/></svg>

<div class="abs brand" style="left:58px;top:32px"><span class="brand-dot"></span>Bright Neighbour</div>
<nav class="abs nav-links"><a class="active">Home</a><a>About Us</a><a>Our Story</a><a>Social Impact</a><a>Join Us</a></nav>
<a class="abs btn" style="left:1028px;top:27px;width:112px;height:43px">Sign Up</a>

<h1 class="abs h1" style="left:60px;top:280px">New way of Giving<br><span class="accent">Social Inclusion</span></h1>
<p class="abs lead" style="left:60px;top:392px;width:380px">We believe in authentic social responsibility is driven<br>from individuals and businesses.</p>
<a class="abs btn" style="left:60px;top:463px;width:158px;height:42px">Sign Up Now</a>
<div class="abs phones" role="img" aria-label="App screens on three phones showing product search, featured merchants and the token wallet"></div>

<div class="abs eyebrow" style="left:0;width:1200px;text-align:center;top:809px">Our Partners</div>
<div class="abs partners">
  <div class="cell" style="left:0;top:0">Corvane Media Authority</div>
  <div class="cell" style="left:181px;top:0">Ashfield Poly</div>
  <div class="cell" style="left:362px;top:0">Westbrook University</div>
  <div class="cell" style="left:543px;top:0">Harbor Hub</div>
  <div class="cell" style="left:724px;top:0">Northvale University</div>
  <div class="cell" style="left:0;top:98px">Kindle Action Network</div>
  <div class="cell" style="left:181px;top:98px"></div>
  <div class="cell" style="left:362px;top:98px">Enterprise Lumen</div>
  <div class="cell" style="left:543px;top:98px"></div>
  <div class="cell" style="left:724px;top:98px">Tessel Ventures</div>
  <div class="cell" style="left:181px;top:196px">Rydo</div>
  <div class="cell" style="left:362px;top:196px"></div>
  <div class="cell" style="left:543px;top:196px">Halvor Bank</div>
  <div class="cell" style="left:362px;top:294px">Marrow Holdings</div>
</div>

<h2 class="abs section-title" style="top:1331px">Why Us?</h2>
<div class="abs why-art" role="img" aria-label="Colourful flat illustration of people sharing and giving"></div>

<div class="abs feat-icon" style="left:630px;top:1443px"><svg width="40" height="40" viewBox="0 0 40 40" fill="none" stroke="#fff" stroke-width="2"><circle cx="22" cy="14" r="8"/><path d="M22 10v8M19.5 12h4a1.5 1.5 0 010 3h-3a1.5 1.5 0 000 3h4"/><path d="M4 30h8l6 3h12l6-5"/></svg></div>
<div class="abs feat-title" style="left:738px;top:1446px">Affordable</div>
<p class="abs feat-text" style="left:738px;top:1474px">Doing good does not need to be only on a large scale.<br>We make it practical and resourceful.</p>

<div class="abs feat-icon" style="left:630px;top:1585px"><svg width="40" height="40" viewBox="0 0 40 40" fill="none" stroke="#fff" stroke-width="2.2"><circle cx="17" cy="17" r="11"/><path d="M25 25l9 9"/></svg></div>
<div class="abs feat-title" style="left:738px;top:1588px">Transparent</div>
<p class="abs feat-text" style="left:738px;top:1616px">Monitor your account to see where each contribution<br>of yours goes.</p>

<div class="abs feat-icon" style="left:630px;top:1727px"><svg width="40" height="40" viewBox="0 0 40 40" fill="none" stroke="#fff" stroke-width="2"><path d="M5 5v30h30"/><path d="M9 28l6-9 5 5 6-10 6 4"/></svg></div>
<div class="abs feat-title" style="left:738px;top:1730px">Measurable</div>
<p class="abs feat-text" style="left:738px;top:1758px">Access your account any time to view the full<br>contributions report.</p>

<div class="abs card" style="left:60px">
  <svg width="48" height="44" viewBox="0 0 48 44" fill="none" stroke="var(--pink)" stroke-width="1.6"><circle cx="24" cy="8" r="5"/><circle cx="10" cy="14" r="4"/><circle cx="38" cy="14" r="4"/><path d="M16 40V24a8 8 0 0116 0v16M4 40V28a6 6 0 0110 -4M44 40V28a6 6 0 00-10-4"/></svg>
  <h3>Bright Neighbours</h3>
  <p>You might be a busy professional with a strong desire to help our community practically.</p>
  <a class="more">READ MORE</a>
</div>
<div class="abs card" style="left:337px">
  <svg width="48" height="44" viewBox="0 0 48 44" fill="none" stroke="var(--pink)" stroke-width="1.6"><path d="M6 42h36M12 42V16h12v26M24 42V6h12v36M28 12h4M28 18h4M28 24h4M16 22h4M16 28h4"/></svg>
  <h3>Bright Business</h3>
  <p>Traditionally, Corporate Social Responsibility (CSR) has been for the "big guys" who run...</p>
  <a class="more">READ MORE</a>
</div>
<div class="abs card" style="left:615px">
  <svg width="48" height="44" viewBox="0 0 48 44" fill="none" stroke="var(--pink)" stroke-width="1.6"><path d="M4 14l4-10h32l4 10zM4 14v4a5 5 0 0010 0 5 5 0 0010 0 5 5 0 0010 0 5 5 0 0010 0v-4M7 22v20h34V22M12 42V30h10v12M28 30h8v6h-8z"/></svg>
  <h3>Merchant</h3>
  <p>In Bright Neighbour, we make it convenient and easy to blend social impact to your shop...</p>
  <a class="more">READ MORE</a>
</div>
<div class="abs card" style="left:892px">
  <svg width="48" height="44" viewBox="0 0 48 44" fill="none" stroke="var(--pink)" stroke-width="1.6"><rect x="6" y="14" width="36" height="8"/><rect x="9" y="22" width="30" height="20"/><path d="M24 14v28M24 14c-4-10-14-8-10-2M24 14c4-10 14-8 10-2"/></svg>
  <h3>The Bright Gift</h3>
  <p>Unique Gift, Real Impact - A gift that meaningfully connects people to do good together.</p>
  <a class="more">READ MORE</a>
</div>

<div class="abs eyebrow" style="left:60px;top:2331px">About Us</div>
<h2 class="abs h1" style="left:60px;top:2353px;font-size:42px">Hello, Bright Neighbours!</h2>
<p class="abs lead" style="left:60px;top:2422px;width:480px;font-size:12.5px">Just like you, we resonate with a variety of social causes. At the core of everything, we believe that many societal challenges could be minimized merely by being more kind to one another and showing more trust in each other, especially during these difficult times.</p>
<a class="abs btn" style="left:60px;top:2555px;width:142px;height:43px">Read More</a>
<div class="abs video" role="img" aria-label="Illustrated city skyline with a winding path, video thumbnail"></div>
<svg class="abs" style="left:848px;top:2432px" width="58" height="58" viewBox="0 0 58 58" aria-hidden="true"><circle cx="29" cy="29" r="27" fill="#fff" fill-opacity=".9"/><path d="M24 19l15 10-15 10z" fill="var(--pink)"/></svg>

<div class="abs eyebrow" style="left:0;width:1200px;text-align:center;top:2708px">Social Impact</div>
<h2 class="abs section-title" style="top:2733px">Our Social Impact<br>Ambassadors and Mentors</h2>

<div class="abs member" style="left:60px"><div class="photo" role="img" aria-label="Portrait photo of a mentor" style="background:linear-gradient(180deg,#4f5257,#2f3136)"></div><div class="meta"><b>Name</b>Company<br>Designation</div></div>
<div class="abs member featured" style="left:337px"><div class="photo" role="img" aria-label="Portrait photo of an ambassador" style="background:linear-gradient(180deg,#c9d3c0,#e8dcd2)"></div><div class="meta"><b>Name</b>Company<br>Designation</div></div>
<div class="abs member" style="left:615px"><div class="photo" role="img" aria-label="Portrait photo of a mentor" style="background:linear-gradient(180deg,#e9e9ea,#3a3d44)"></div><div class="meta"><b>Name</b>Company<br>Designation</div></div>
<div class="abs member" style="left:892px"><div class="photo" role="img" aria-label="Portrait photo of an ambassador" style="background:linear-gradient(180deg,#f1ece8,#d8c3b6)"></div><div class="meta"><b>Name</b>Company<br>Designation</div></div>

<div class="abs gift-art" role="img" aria-label="Pink gift card reading pay it forward with a ten dollar badge and gift icons"></div>
<div class="abs eyebrow" style="left:602px;top:3343px">Simple . Fun . Impactful.</div>
<h2 class="abs h1" style="left:602px;top:3366px">Inspire others with<br>a meaningful gift.</h2>
<p class="abs gi-text" style="left:602px;top:3494px">Unique Gift, Real Impact - A gift that meaningfully connects people to<br>do good together.</p>

<div class="abs feat-icon" style="left:588px;top:3575px"><svg width="40" height="40" viewBox="0 0 48 44" fill="none" stroke="#fff" stroke-width="2"><rect x="6" y="14" width="36" height="8"/><rect x="9" y="22" width="30" height="20"/><path d="M24 14v28M24 14c-4-10-14-8-10-2M24 14c4-10 14-8 10-2"/></svg></div>
<div class="abs gi-title" style="left:697px;top:3579px">Gift &amp; Giving</div>
<p class="abs gi-text" style="left:697px;top:3606px">Be it a corporate gift, a giveaway for a unique<br>occasion, or an entirely new approach... <a>READ MORE</a></p>

<div class="abs feat-icon" style="left:588px;top:3702px"><svg width="40" height="40" viewBox="0 0 40 40" fill="none" stroke="#fff" stroke-width="2"><path d="M5 18h7v17H5zM12 33h16a3 3 0 003-3l3-10a3 3 0 00-3-3h-9l1-7a3 3 0 00-5-2l-6 10"/></svg></div>
<div class="abs gi-title" style="left:697px;top:3706px">Inspire Kindness</div>
<p class="abs gi-text" style="left:697px;top:3733px">Create a brand-new experience and inspire someone<br>to participate in the ripple effect of... <a>READ MORE</a></p>

<div class="abs footer"></div>
<svg class="abs" style="left:0;top:3905px" width="1200" height="50" viewBox="0 0 1200 50" aria-hidden="true"><path d="M0 25 C300 5 800 50 1200 20 L1200 50 L0 50Z" fill="var(--lav)"/></svg>

<div class="abs brand" style="left:60px;top:3990px"><span class="brand-dot" style="width:40px;height:40px"></span>Bright Neighbour</div>
<div class="abs f-head" style="left:60px;top:4057px">Follow us and stay updated!</div>
<p class="abs f-text" style="left:60px;top:4083px;width:250px">A Singapore Social Enterprise.<br>In a world where you can be anything,<br>be kind.</p>
<div class="abs social solid" style="left:62px;top:4162px" aria-label="Social network"></div>
<div class="abs social" style="left:100px;top:4162px" aria-label="Social network"></div>
<div class="abs social" style="left:137px;top:4162px" aria-label="Social network"></div>
<div class="abs social" style="left:175px;top:4162px" aria-label="Social network"></div>

<div class="abs f-head" style="left:338px;top:3985px">Useful Links</div>
<div class="abs f-links" style="left:338px;top:4020px">Home<br>About Us<br>Our Story<br>Social Impact<br>Bright Neighbour</div>
<div class="abs f-links" style="left:617px;top:4020px">Bright Business<br>Merchant<br>The Bright Gift<br>FAQs<br>Contact Us</div>

<div class="abs f-head" style="left:895px;top:3985px">Subscribe to Our Newsletter</div>
<p class="abs f-text" style="left:895px;top:4010px;width:245px">Let's stay in touch! We would like to keep you inspired with our Kindness stories and community events.</p>
<div class="abs input">Enter email here...</div>
<div class="abs" style="left:895px;top:4128px;width:12px;height:12px;border:1px solid #c9c9d0;background:#fff"></div>
<p class="abs f-text" style="left:912px;top:4124px;width:230px">By continuing, you accept the privacy policy</p>
<a class="abs btn" style="left:895px;top:4175px;width:245px;height:42px">Subscribe Now</a>

<div class="abs" style="left:60px;top:4245px;width:1080px;height:1px;background:var(--line)"></div>
<p class="abs" style="left:0;width:1200px;top:4262px;text-align:center;font-size:11px">© <span style="color:var(--pink)">BRIGHT NEIGHBOUR SINGAPORE</span> - 2021. All Rights Reserved.</p>

</body>
</html>
```